Kor'v Meridell Travel

We need a sleek, professional, inviting card to elicit global travel for the experienced and professional traveler. Royal blue, black and silver. (perhaps the wording could be silver with black shadow?-get creative) Maybe a watermark on the front and the full raised logo on the back.
We want a stylish and modern card, but professional.

```html
<!DOCTYPE html>
<html lang="en">
<head>
<meta charset="utf-8">
<title>Kor'v Meridell Travel — Business Card</title>
<link href="https://fonts.googleapis.com/css2?family=Open+Sans:ital,wght@0,400;0,700;0,800;1,700&display=swap" rel="stylesheet">
<style>
  :root {
    --stage: #1c1c1c;
    --card: #1e1e1f;
    --card-edge: #2a2a2b;
    --blue: #1ea0e6;
    --green: #7fc241;
    --text: #c9c9c9;
    --silver: #9a9a9c;
  }
  * { margin: 0; padding: 0; box-sizing: border-box; }
  html, body { width: 1200px; height: 900px; overflow: hidden; }
  body {
    background: var(--stage);
    font-family: "Open Sans", sans-serif;
    display: flex;
    flex-direction: column;
    align-items: center;
    justify-content: center;
    gap: 60px;
  }
  .card {
    position: relative;
    width: 630px;
    height: 360px;
    background: var(--card);
    border: 1px solid var(--card-edge);
    box-shadow: 0 12px 30px rgba(0,0,0,0.5);
  }

  /* Front */
  .brand {
    position: absolute;
    top: 46px;
    left: 48px;
    display: flex;
    align-items: center;
    gap: 12px;
  }
  .brand-dot {
    width: 18px; height: 18px;
    border-radius: 50%;
    background: var(--blue);
  }
  .brand-name {
    font-weight: 800;
    font-size: 22px;
    letter-spacing: 1px;
    color: var(--blue);
    text-transform: uppercase;
  }
  .divider {
    position: absolute;
    left: 48px;
    right: 48px;
    top: 176px;
    height: 1px;
    background: var(--blue);
  }
  .contacts {
    position: absolute;
    left: 48px;
    top: 106px;
    list-style: none;
    font-size: 14px;
    color: var(--text);
    line-height: 20px;
  }
  .contacts li { display: flex; align-items: center; gap: 9px; }
  .contacts svg { width: 11px; height: 11px; fill: var(--green); flex: none; }
  .person {
    position: absolute;
    right: 48px;
    top: 196px;
    text-align: right;
  }
  .person-name {
    font-weight: 700;
    font-style: italic;
    font-size: 24px;
    color: var(--blue);
    text-transform: uppercase;
  }
  .person-role {
    font-size: 16px;
    color: var(--text);
    margin-top: 2px;
  }
  .address {
    position: absolute;
    right: 48px;
    bottom: 40px;
    text-align: right;
    font-size: 16px;
    line-height: 22px;
    color: var(--text);
  }

  /* Back */
  .card-back {
    display: flex;
    align-items: center;
    justify-content: center;
  }
  .back-name {
    font-weight: 800;
    font-size: 34px;
    letter-spacing: 3px;
    color: var(--silver);
    text-transform: uppercase;
  }
</style>
</head>
<body>

  <section class="card card-front">
    <div class="brand">
      <span class="brand-dot"></span>
      <span class="brand-name">Kor'v Meridell Travel</span>
    </div>

    <ul class="contacts">
      <li>
        <svg viewBox="0 0 12 12" aria-hidden="true"><path d="M2.5 0.8 4.3 3 3.4 4.3c.6 1.6 1.7 2.7 3.3 3.3L8 6.7l2.2 1.8-.8 2.2C5 10.4 1.6 7 1.2 2.6z"/></svg>
        555-301-7782
      </li>
      <li>
        <svg viewBox="0 0 12 12" aria-hidden="true"><path d="M0 2h12v1.2L6 7 0 3.2zM0 4.6l6 3.8 6-3.8V10H0z"/></svg>
        info@korvmeridell.com
      </li>
      <li>
        <svg viewBox="0 0 12 12" aria-hidden="true"><circle cx="6" cy="6" r="5.5"/></svg>
        www.korvmeridell.com
      </li>
    </ul>

    <div class="divider"></div>

    <div class="person">
      <p class="person-name">Darin Holloway</p>
      <p class="person-role">President</p>
    </div>

    <address class="address" style="font-style:normal">
      1870 Crestline Harbor<br>
      Solana Vista CA 90417
    </address>
  </section>

  <section class="card card-back">
    <p class="back-name">Kor'v Meridell Travel</p>
  </section>

</body>
</html>
```